Professional Baby Bottle Bank Print Design

We need a baby bottle design that is 4.25" wide x 2.28" tall with a maximum of 6 colors (white is counted as a color).

The bottle design needs to be fun but professional. Bottles with cartoon images on it will be rejected immediately.

The bottle design wraps around the bottle. See examples here: https://vel.quin/cat/BabyBottles/HarlowBottles/5

Minimum font size is 10pt.

The bottle design must have the following text on it:
Main Text: Hold Them Close
Paragraph text: Our ministry’s aim is to not only save unborn babies, but to provide love, support, and life-saving resources for vulnerable women in our community. By filling this bottle with cash, checks, and spare coins and returning it on collection day, you are truly saving and changing lives!
Optional text: Thank you!

We are including an example file and a template file. You do NOT have to use the template - but your file has to be the exact size mentioned. If you don't design as well as our sample, please don't waste our time by spamming us with hundreds of designs. We will ban design houses that spam us with designs that are more layouts (and not well designed).

Please note - white is a color. You don't have to do a box - but anything you don't make white will be see-through.

We will take the winners of this contest to a survey with the customers. We may choose two and edit the text of one slightly to be different. We must know the fonts used.

No gradients unless they are half-toned with relatively big sized dots.

Target Market(s)

Church Attendees coming from a Pregnancy Center

Industry/Entity Type

Religious Christian Churches

Requirements
Must have
• Professional, great palette, wording as described.
Nice to have
• Integrated design across the whole space with areas for text (no text all the way across)
Should not have
• Cartoon figures; elements shoved together that don't go together (i.e. - actually design something)

```html
<!DOCTYPE html>
<html lang="en">
<head>
<meta charset="utf-8">
<title>Hold Them Close – Baby Bottle Label</title>
<link rel="stylesheet" href="https://fonts.googleapis.com/css2?family=Cormorant+Garamond:ital,wght@0,600;1,600&family=Great+Vibes&display=swap">
<style>
  :root {
    --backdrop: #bcdcd6;
    --label-white: #fdfcfd;
    --magenta: #c42b80;
    --blush: #f08bbb;
    --navy: #2f4a7a;
    --white: #ffffff;
  }
  * { margin: 0; padding: 0; box-sizing: border-box; }
  html, body {
    width: 1200px; height: 1200px; overflow: hidden;
    background: var(--backdrop);
  }
  .canvas {
    position: relative; width: 1200px; height: 1200px;
    display: flex; align-items: center; justify-content: center;
  }
  .label {
    position: relative; width: 1120px; height: 601px;
    background: var(--label-white); overflow: hidden;
  }
  .label__wave { position: absolute; inset: 0; width: 100%; height: 100%; }
  .campaign-name {
    position: absolute; left: 50px; top: 88px; width: 220px;
    font-family: "Cormorant Garamond", serif; font-weight: 600; font-style: normal;
    font-size: 46px; line-height: 1.08; color: var(--navy);
    text-align: center; letter-spacing: 2px; text-transform: uppercase;
  }
  .campaign-name span { display: block; }
  .accent { position: absolute; background: var(--blush); border-radius: 50%; }
  .accent--top-heart { left: 40px; top: 40px; width: 36px; height: 36px; opacity: .8; }
  .accent--left-heart { left: 140px; top: 320px; width: 38px; height: 36px; }
  .accent--right-heart { left: 560px; top: 380px; width: 40px; height: 38px; }
  .accent--butterfly { left: 452px; top: 52px; width: 110px; height: 90px; border-radius: 40% 40% 48% 48%; }
  .portrait {
    position: absolute; left: 272px; top: 160px; width: 268px; height: 340px;
    border-radius: 50% 50% 46% 46%;
    background: radial-gradient(circle at 45% 40%, #d4479a, var(--magenta));
  }
  .mission {
    position: absolute; left: 585px; top: 42px; width: 500px;
    font-family: "Cormorant Garamond", serif; font-style: italic; font-weight: 600;
    font-size: 28px; line-height: 38px; color: var(--navy); text-align: center;
  }
  .thanks {
    position: absolute; left: 620px; top: 500px; width: 420px;
    font-family: "Great Vibes", cursive; font-size: 66px; color: var(--white);
    text-align: center; line-height: 1;
  }
</style>
</head>
<body>
  <main class="canvas">
    <section class="label">
      <svg class="label__wave" viewBox="0 0 1120 601" preserveAspectRatio="none" aria-hidden="true">
        <path fill="var(--magenta)" d="M0 358 C 120 352 220 320 280 230 C 320 170 380 200 400 300 C 430 440 520 500 640 490 C 800 478 950 440 1120 445 L1120 601 L0 601 Z"/>
      </svg>

      <div class="accent accent--top-heart" role="img" aria-label="Small outlined heart doodle"></div>
      <h1 class="campaign-name">
        <span>Hold</span>
        <span>Them</span>
        <span>Close</span>
      </h1>
      <div class="accent accent--left-heart" role="img" aria-label="Small pink hearts"></div>

      <div class="portrait" role="img" aria-label="Silhouette of a mother holding her baby"></div>
      <div class="accent accent--butterfly" role="img" aria-label="Pink butterfly"></div>
      <div class="accent accent--right-heart" role="img" aria-label="Small pink hearts"></div>

      <p class="mission">Our ministry’s aim is to not only save unborn babies, but to provide love, support, and life-saving resources for vulnerable women in our community. By filling this bottle with cash, checks, and spare coins and returning it on collection day, you are truly saving and changing lives!</p>

      <p class="thanks">Thank You</p>
    </section>
  </main>
</body>
</html>
```